Business Card for a Dental Office

The design should communicate integrity, quality and reliability. We also want the card look elegant, simple, but still stand out, different from the traditional-dental-office business card.

Industry/Entity Type

Business

```html
<!DOCTYPE html>
<html lang="en">
<head>
<meta charset="utf-8">
<title>Harlow Dental Centre – Business Card</title>
<link href="https://fonts.googleapis.com/css2?family=Oswald:wght@500;600&family=Open+Sans:wght@400;600&display=swap" rel="stylesheet">
<style>
  :root {
    --page-bg: #d8d1c3;
    --card-light: #a98d3d;
    --card-mid: #917628;
    --card-dark: #7a621e;
    --ink-white: #f7f4ea;
    --accent: #d6d04a;
    --rule: rgba(255, 255, 255, 0.85);
  }
  * { margin: 0; padding: 0; box-sizing: border-box; }
  html, body {
    width: 1200px;
    height: 1022px;
    overflow: hidden;
    background: var(--page-bg);
  }
  .stage {
    width: 1200px;
    height: 1022px;
    display: flex;
    align-items: center;
    justify-content: center;
  }
  .card {
    position: relative;
    width: 1000px;
    height: 572px;
    background: linear-gradient(135deg, var(--card-light) 0%, var(--card-mid) 45%, var(--card-dark) 100%);
    box-shadow: 0 18px 40px rgba(60, 45, 20, 0.35);
    overflow: hidden;
  }
  .divider {
    position: absolute;
    top: 0;
    left: 700px;
    width: 2px;
    height: 100%;
    background: var(--rule);
  }
  .brand {
    position: absolute;
    left: 70px;
    top: 92px;
    display: flex;
    align-items: center;
    gap: 22px;
  }
  .brand-mark {
    width: 84px;
    height: 84px;
    background: var(--accent);
    flex: none;
  }
  .brand-name {
    font-family: "Oswald", sans-serif;
    font-weight: 600;
    font-size: 40px;
    line-height: 1;
    letter-spacing: 0.5px;
    color: var(--ink-white);
    text-transform: uppercase;
  }
  .brand-tagline {
    margin-top: 8px;
    font-family: "Open Sans", sans-serif;
    font-weight: 600;
    font-size: 15px;
    letter-spacing: 0.6px;
    color: var(--accent);
    text-transform: uppercase;
  }
  .contact {
    position: absolute;
    left: 70px;
    bottom: 58px;
    width: 630px;
  }
  .person-name {
    font-family: "Oswald", sans-serif;
    font-weight: 500;
    font-size: 34px;
    line-height: 1.1;
    letter-spacing: 1px;
    color: var(--ink-white);
    text-transform: uppercase;
  }
  .person-role {
    display: flex;
    align-items: center;
    gap: 14px;
    margin-top: 2px;
    font-family: "Open Sans", sans-serif;
    font-size: 17px;
    letter-spacing: 1px;
    color: var(--accent);
    text-transform: uppercase;
  }
  .person-role::after {
    content: "";
    flex: 1;
    height: 1px;
    background: var(--rule);
  }
  .details {
    list-style: none;
    margin-top: 14px;
  }
  .details li {
    display: flex;
    align-items: center;
    gap: 14px;
    font-family: "Open Sans", sans-serif;
    font-size: 19px;
    line-height: 30px;
    color: var(--ink-white);
  }
  .details svg {
    width: 16px;
    height: 16px;
    flex: none;
  }
</style>
</head>
<body>
<main class="stage">
  <section class="card">
    <div class="divider"></div>

    <header class="brand">
      <div class="brand-mark"></div>
      <div>
        <h1 class="brand-name">Harlow Dental Centre</h1>
        <p class="brand-tagline">Your smile is your gift to others</p>
      </div>
    </header>

    <div class="contact">
      <h2 class="person-name">Elias Marren</h2>
      <p class="person-role">Director</p>
      <ul class="details">
        <li>
          <svg viewBox="0 0 16 16" aria-hidden="true"><path d="M3 1.5l3 .5 1 3.2-1.7 1.3a8 8 0 0 0 4.2 4.2L10.8 9l3.2 1 .5 3-1.8 1.8C6.8 14.6 1.4 9.2 1.2 3.3z" fill="#d6d04a"/></svg>
          +330 5127-3904
        </li>
        <li>
          <svg viewBox="0 0 16 16" aria-hidden="true"><rect x="1" y="3" width="14" height="10" fill="#d6d04a"/><path d="M1.5 3.5L8 9l6.5-5.5" stroke="#7a621e" stroke-width="1.4" fill="none"/></svg>
          info@harlowdentalcentre.com
        </li>
        <li>
          <svg viewBox="0 0 16 16" aria-hidden="true"><circle cx="8" cy="8" r="7" fill="#d6d04a"/><path d="M1 8h14M8 1c-3 3.5-3 10.5 0 14M8 1c3 3.5 3 10.5 0 14" stroke="#7a621e" stroke-width="1.1" fill="none"/></svg>
          www.harlowdentalcentre.com
        </li>
      </ul>
    </div>
  </section>
</main>
</body>
</html>
```